Flat bootstrap design for existing site

I'm looking for a modern flat design based around an existing logo. This has to be a custom design (no external templates), and implemented into a bootstrap framework.

The logo is attached as 2 versions - choose whichever you want, that flows better with whatever design you choose.

Added screenshots of the existing site (currently using the default bootstrap layouts). Please make your designs around those pages in the screenshots (i.e. the homepage only has the postal code input and the header). The active page has 3 screenshots, because I wanted to illustrate the other states that would be visible (in the table rows).

This is a moving/junk removal website, just for some context.

Here's some example websites (flat designs) that I like, just to give you an idea of what I'm after.

https://www.plimvora.com/
https://dacklow.com/
https://trevanu.com/
https://quobrintal.com/en/

Coding

Coded - Design and coding required

Number of Pages Required

5+ page

Colors

Designer to choose colors to be used in the design.

Requirements
Must have
• It must be a modern/simple flat design, that is built around the existing logo (attached).
• It has to be implemented using bootstrap.

```html
<!DOCTYPE html>
<html lang="en">
<head>
<meta charset="utf-8">
<title>Haulbeam – Book Details</title>
<link rel="stylesheet" href="https://fonts.googleapis.com/css2?family=Mulish:wght@400;600;700;800&family=Nunito:wght@700;800&display=swap">
<style>
  :root {
    --sky: #4ac7f4;
    --sky-light: #8cdcf8;
    --page: #e6e6e6;
    --white: #ffffff;
    --ink: #2f2f2f;
    --ink-soft: #555555;
    --muted: #7a7a7a;
    --nav: #6b6b6b;
    --heading-grey: #777777;
    --rule: #cfcfcf;
    --table-head: #ececec;
    --green: #8dcd38;
    --link: #1a9fd6;
    --pending: #666666;
    --footer: #f5f5f5;
  }
  * { box-sizing: border-box; margin: 0; padding: 0; }
  html, body { width: 1200px; height: 1100px; overflow: hidden; }
  body {
    position: relative;
    background: var(--page);
    font-family: "Mulish", sans-serif;
    color: var(--ink);
  }
  .site-header {
    position: absolute; left: 0; top: 0; width: 1200px; height: 114px;
    background: var(--white);
  }
  .brand {
    position: absolute; left: 82px; top: 32px;
    display: flex; align-items: center; gap: 10px;
    font-family: "Mulish", sans-serif; font-weight: 800; font-size: 36px;
    color: var(--sky); letter-spacing: 1px;
  }
  .brand-dot { width: 22px; height: 22px; border-radius: 50%; background: var(--sky); }
  .main-nav {
    position: absolute; left: 470px; top: 45px;
    display: flex; gap: 39px;
    font-size: 17px; letter-spacing: .5px; color: var(--nav);
  }
  .account {
    position: absolute; left: 933px; top: 46px;
    font-size: 15px; color: var(--nav);
    display: flex; align-items: center; gap: 6px;
  }
  .book-panel {
    position: absolute; left: 86px; top: 147px; width: 1028px; height: 363px;
    background: var(--sky); color: var(--white);
  }
  .panel-title {
    position: absolute; left: 46px; top: 32px;
    font-family: "Nunito", sans-serif; font-weight: 800; font-size: 30px;
  }
  .field-label { position: absolute; font-size: 18px; font-weight: 600; line-height: 22px; }
  .field {
    position: absolute; height: 45px; background: var(--white);
    box-shadow: 0 2px 4px rgba(0,0,0,.15);
    display: flex; align-items: center; justify-content: space-between;
    padding: 0 12px; font-size: 16px; color: var(--muted);
  }
  .btn-update {
    position: absolute; left: 42px; top: 278px; width: 157px; height: 48px;
    border: 3px solid var(--white); border-radius: 26px;
    display: flex; align-items: center; justify-content: center;
    font-family: "Nunito", sans-serif; font-weight: 700; font-size: 18px;
  }
  .section-title {
    position: absolute; left: 93px; top: 552px;
    font-family: "Nunito", sans-serif; font-weight: 800; font-size: 30px;
    color: var(--heading-grey);
  }
  .notice {
    position: absolute; left: 91px; top: 606px; width: 1028px; height: 49px;
    background: var(--sky-light); color: var(--white);
    padding-left: 36px; line-height: 49px; font-size: 16px;
  }
  .drivers-card {
    position: absolute; left: 91px; top: 655px; width: 1028px; height: 314px;
    background: var(--white);
  }
  .drivers-head {
    position: absolute; left: 28px; top: 18px; width: 957px; height: 40px;
    background: var(--table-head);
    font-size: 16px; font-weight: 600; color: var(--ink);
  }
  .drivers-head span, .driver-row span { position: absolute; top: 50%; transform: translateY(-50%); white-space: nowrap; }
  .driver-row {
    position: absolute; left: 36px; width: 960px; height: 48px;
    font-size: 15px; color: var(--ink-soft);
  }
  .driver-row.ruled { border-bottom: 1px solid var(--rule); }
  .status {
    width: 120px; height: 26px; line-height: 26px; text-align: center;
    font-size: 13px; font-weight: 600; color: var(--white);
  }
  .status.accepted { background: var(--green); }
  .status.sent { background: var(--sky); }
  .status.pending { background: var(--pending); }
  .payment { color: var(--link); font-size: 16px; }
  .site-footer {
    position: absolute; left: 0; top: 1019px; width: 1200px; height: 81px;
    background: var(--footer);
    text-align: center; line-height: 70px; font-size: 16px; color: var(--muted);
    padding-right: 13px;
  }
</style>
</head>
<body>
  <header class="site-header">
    <div class="brand"><span class="brand-dot"></span>Haulbeam</div>
    <nav class="main-nav"><span>BOOK</span><span>HOW IT WORKS</span><span>BECOME A DRIVER</span></nav>
    <div class="account">mara@tovelin.com
      <svg width="16" height="10" viewBox="0 0 16 10"><path d="M1 1l7 7 7-7" fill="none" stroke="#6b6b6b" stroke-width="1.6"/></svg>
    </div>
  </header>

  <section class="book-panel">
    <h1 class="panel-title">Book Details</h1>
    <div class="field-label" style="left:44px;top:82px">Package Selected:</div>
    <div class="field" style="left:44px;top:113px;width:466px">Package 1
      <svg width="18" height="10" viewBox="0 0 18 10"><path d="M1 1l8 8 8-8" fill="none" stroke="#777" stroke-width="1.6"/></svg>
    </div>
    <div class="field-label" style="left:523px;top:82px">Pick-up time selected</div>
    <div class="field" style="left:522px;top:113px;width:466px">July 18 at 4:13 am
      <svg width="18" height="18" viewBox="0 0 18 18" fill="none" stroke="#999" stroke-width="1.2"><rect x="1" y="3" width="16" height="14"/><path d="M1 7h16M5 1v4M13 1v4M5 10h2M9 10h2M13 10h1M5 13h2M9 13h2M13 13h1"/></svg>
    </div>
    <div class="field-label" style="left:46px;top:178px">Description</div>
    <div class="field" style="left:46px;top:209px;width:942px">1 Large stove<span></span></div>
    <div class="btn-update">Update</div>
  </section>

  <h2 class="section-title">Drivers in your area</h2>
  <div class="notice">Please stay on this page and be patient, while we contact the driver and find you one ASAP</div>

  <section class="drivers-card">
    <div class="drivers-head">
      <span style="left:21px">Name</span>
      <span style="left:198px">Distance</span>
      <span style="left:398px">Agreed pick-up time</span>
    </div>
    <div class="driver-row ruled" style="top:66px">
      <span style="left:2px">Dorian Vell</span>
      <span style="left:176px">4.04 km away</span>
      <span style="left:369px">July 18 at 4:13 am</span>
      <span class="status accepted" style="left:608px">Time accepted</span>
      <span class="payment" style="left:835px">Payment made</span>
    </div>
    <div class="driver-row ruled" style="top:114px">
      <span style="left:2px">Ansel Brody</span>
      <span style="left:176px">5.75 km away</span>
      <span style="left:369px">-</span>
      <span class="status sent" style="left:609px">Request sent</span>
    </div>
    <div class="driver-row ruled" style="top:162px;height:52px">
      <span style="left:2px">Cyril Maddox</span>
      <span style="left:176px">11.13 km away</span>
      <span style="left:369px">-</span>
      <span class="status sent" style="left:609px">Request sent</span>
    </div>
    <div class="driver-row" style="top:214px">
      <span style="left:2px">Roland Pike</span>
      <span style="left:176px">11.91 km away</span>
      <span style="left:369px">-</span>
      <span class="status pending" style="left:611px">Pending</span>
    </div>
  </section>

  <footer class="site-footer">© 2017 Company Name&nbsp; All right reserved&nbsp; Term of Use</footer>
</body>
</html>
```